Health Supplement Series for 60 tablets of pure Amber Vine Core powder

We need a packaging design theme for a health supplement for international consumers. Our initial product is called 'Amber Vine Core'. It is for general health and is particularly effective for diabetic symptoms.
We would like to see designs that are clean and fresh.
It should give the impression of professional, premium pharmaceutical grade products.
Our company logo is attached below.

Target Market(s)

International

Industry/Entity Type

Health And Wellness

Font styles to use
Serif
Sans Serif

Requirements
Must have
• Bottle and box packaging required.
• 1st product is bottle of 60 tablets of 0.5gm each.
Should not have
• Seals and other "must buy" "guaranteed" etc

```html
<!DOCTYPE html>
<html lang="en">
<head>
<meta charset="UTF-8">
<title>Amber Vine Core – Verdant Labs Limited</title>
<link rel="stylesheet" href="https://fonts.googleapis.com/css2?family=Cinzel:wght@400;600&family=Open+Sans:wght@600&family=PT+Serif&family=Roboto+Condensed:wght@400;700&display=swap">
<style>
  :root{
    --bg:#e6e6e6;
    --panel:#ffffff;
    --green:#5a9e3a;
    --green-dark:#3f7f26;
    --green-light:#8cc46a;
    --ink:#1c1c1c;
    --seed-a:#e0a466;
    --seed-b:#a8652d;
  }
  *{margin:0;padding:0;box-sizing:border-box}
  html,body{width:1200px;height:1200px;overflow:hidden;background:var(--bg)}
  .canvas{position:relative;width:1200px;height:1200px}
  .box-side,.box-front{position:absolute;top:290px;height:620px;background:var(--panel);box-shadow:0 4px 14px rgba(0,0,0,.08)}
  .box-side{left:240px;width:300px;padding:22px 20px;font-family:"Roboto Condensed",sans-serif;color:var(--ink)}
  .box-front{left:540px;width:420px;overflow:hidden}

  .facts{border:2px solid var(--ink);border-radius:6px;padding:8px 10px;font-size:11px;line-height:1.35}
  .facts h2{font-size:22px;font-weight:700;line-height:1.1;border-bottom:6px solid var(--ink);padding-bottom:4px;margin-bottom:4px}
  .facts .rule{border-bottom:1px solid var(--ink);padding:2px 0}
  .facts .rule.thick{border-bottom-width:4px}
  .facts .row{display:flex;justify-content:space-between}
  .facts .note{font-size:10px;padding-top:4px}
  .facts .other{font-size:10px;padding-top:6px}
  .facts b{font-weight:700}
  .storage{font-size:13px;margin-top:16px;line-height:1.5}
  .disclaimer{border:1px solid var(--ink);font-size:9px;padding:6px 8px;margin-top:14px;line-height:1.4}

  .brand{position:absolute;left:50px;top:170px;display:flex;align-items:center;gap:12px;color:var(--green)}
  .brand-mark{width:44px;height:58px;background:var(--green)}
  .brand-name{font-family:"Open Sans",sans-serif;font-weight:600;line-height:1}
  .brand-name .main{display:block;font-size:42px;letter-spacing:4px}
  .brand-name .sub{display:block;font-size:16px;letter-spacing:1px;margin-top:4px}
  .product-title{position:absolute;left:0;width:420px;top:258px;text-align:center;font-family:"Cinzel",serif;font-weight:600;color:var(--green);font-size:44px;line-height:1.2}
  .band{position:absolute;left:0;top:0}
  .seed-photo{position:absolute;left:215px;top:440px;width:185px;height:130px;border-radius:50%;background:radial-gradient(ellipse at 45% 40%,var(--seed-a),var(--seed-b))}
  .count{position:absolute;left:24px;top:525px;font-family:"PT Serif",serif;color:#fff;font-size:17px;line-height:1.4}
  .count .big{font-size:18px;letter-spacing:.5px}
</style>
</head>
<body>
<main class="canvas">
  <section class="box-side">
    <div class="facts">
      <h2>Supplement Facts</h2>
      <div class="rule">Serving Size: 2 Capsules</div>
      <div class="rule thick">Servings Per Container: 30</div>
      <div class="rule"><b>Amount Per Serving</b></div>
      <div class="row"><span>Calcium (as Hydroxycitrate)</span><span>120 mg 12%</span></div>
      <div class="row"><span>Potassium (as Hydroxycitrate)</span><span>180 mg 5%</span></div>
      <div class="row"><span>Amber Vine Core Extract</span><span>1000 mg *</span></div>
      <div class="row rule"><span>Total Active Compounds</span><span>975 mg *</span></div>
      <div class="note">*Daily Value Not Established</div>
      <div class="other"><b>Other Ingredients:</b> Vegetable cellulose capsule. Contains no fillers, binders or artificial ingredients. <b>Does Not Contain:</b> Sugar, yeast, wheat, shellfish, nuts, eggs, dairy or soy.</div>
    </div>
    <p class="storage">Store at 25C (77F); excursions permitted to 15-30C (59-86F)</p>
    <p class="disclaimer">These statements have not been evaluated by the Food and Drug Administration. This product is not intended to diagnose, treat, cure, or prevent any disease.</p>
  </section>

  <section class="box-front">
    <svg class="band" width="420" height="620" viewBox="0 0 420 620" aria-hidden="true">
      <path d="M0 420 C90 360 200 470 420 370 L420 620 L0 620 Z" fill="var(--green)"/>
      <path d="M0 405 C100 350 210 455 420 352" fill="none" stroke="var(--green-light)" stroke-width="5"/>
      <path d="M0 440 C110 390 220 490 420 395" fill="none" stroke="#fff" stroke-width="3" opacity=".7"/>
      <path d="M0 455 C120 410 230 505 420 412" fill="none" stroke="var(--green-dark)" stroke-width="4" opacity=".6"/>
    </svg>
    <div class="brand">
      <span class="brand-mark"></span>
      <span class="brand-name"><span class="main">VERDANT</span><span class="sub">LABS LIMITED</span></span>
    </div>
    <h1 class="product-title">Amber Vine<br>Core</h1>
    <div class="seed-photo" role="img" aria-label="Photo of split amber vine seed on a pile of powder"></div>
    <p class="count"><span class="big">60 TABLETS</span><br>0.5gm each</p>
  </section>
</main>
</body>
</html>
```